The hardcover "Azure Lantern" (large size, Quarto 4º, 12 × 9 1/2 in, 30.5 × 24.15 cm) in German language as follows:

AZURNE LATERNE (title)
Der bemerkenswertesten Gründer und Lenker der Nordregion 2019 (subtitle 1)
KÜSTE UND HINTERLAND (subtitle 2, smaller than subtitle 1)

Brivomark (logo, WMF file attached)

Reason: The solutions are rather too childish and pre-made styles... is there anyone who can make it better? - a professional-looking business book (encyclopedia style, should have no color-pictures, no author's name, logo smaller due to the large size book)

Target Market(s)

business community

Requirements
Must have
• encyclopedia style large size book
must look professional and expensive

Nice to have
• - gold-color hardcover, or some gold-color elements
- some simple and decent graphic element (e.g. an ancient column, or some other architectural detail), if any
Should not have
• no color-pictures
no author's name

```html
<!DOCTYPE html>
<html lang="de">
<head>
<meta charset="utf-8">
<title>Azurne Laterne – Buchcover</title>
<link rel="stylesheet" href="https://fonts.googleapis.com/css2?family=Montserrat:wght@700&family=Cinzel:wght@600;700&display=swap">
<style>
  :root {
    --page: #ffffff;
    --leather-light: #d9b27e;
    --leather-mid: #8a5f2e;
    --leather-dark: #2e1c0c;
    --title-yellow: #ffff00;
    --title-orange: #ff8418;
    --rule-gold: #f2d21c;
    --subtitle: #ffffff;
  }
  html, body {
    margin: 0;
    padding: 0;
    width: 1000px;
    height: 1200px;
    overflow: hidden;
    background: var(--page);
  }
  .canvas {
    position: relative;
    width: 1000px;
    height: 1200px;
  }
  .cover-art {
    position: absolute;
    inset: 0;
  }
  .subtitle-block {
    position: absolute;
    left: 175px;
    width: 688px;
    top: 703px;
    text-align: center;
    font-family: "Cinzel", "Trajan Pro", serif;
    font-weight: 700;
    color: var(--subtitle);
    text-shadow: 0 1px 3px rgba(40, 20, 0, 0.75);
  }
  .subtitle-main {
    margin: 0;
    font-size: 27px;
    line-height: 31px;
    letter-spacing: -0.3px;
  }
  .subtitle-region {
    margin: 12px 0 0;
    font-size: 19px;
    line-height: 22px;
    font-weight: 600;
    text-transform: uppercase;
  }
</style>
</head>
<body>
<div class="canvas">
  <svg class="cover-art" width="1000" height="1200" viewBox="0 0 1000 1200" xmlns="http://www.w3.org/2000/svg">
    <defs>
      <radialGradient id="leather-glow" cx="490" cy="640" r="640" gradientUnits="userSpaceOnUse">
        <stop offset="0" stop-color="var(--leather-light)"/>
        <stop offset="0.4" stop-color="var(--leather-mid)"/>
        <stop offset="1" stop-color="var(--leather-dark)"/>
      </radialGradient>
      <linearGradient id="title-top-fill" x1="205" y1="0" x2="840" y2="0" gradientUnits="userSpaceOnUse">
        <stop offset="0" stop-color="#ff9a1a"/>
        <stop offset="0.28" stop-color="#ffe800"/>
        <stop offset="0.7" stop-color="var(--title-yellow)"/>
        <stop offset="1" stop-color="var(--title-orange)"/>
      </linearGradient>
      <linearGradient id="title-bottom-fill" x1="230" y1="0" x2="830" y2="0" gradientUnits="userSpaceOnUse">
        <stop offset="0" stop-color="var(--title-yellow)"/>
        <stop offset="0.75" stop-color="var(--title-yellow)"/>
        <stop offset="1" stop-color="#ffb31a"/>
      </linearGradient>
    </defs>

    <rect class="cover-leather" x="175" y="92" width="688" height="1038" fill="url(#leather-glow)" role="img" aria-label="Braune Lederstruktur des Buchdeckels"/>

    <g class="book-title" font-family="Montserrat, 'Century Gothic', sans-serif" font-weight="700">
      <text x="210" y="520" font-size="138" textLength="626" lengthAdjust="spacingAndGlyphs" fill="url(#title-top-fill)">AZURNE</text>
      <text x="258" y="682" font-size="150" textLength="546" lengthAdjust="spacingAndGlyphs" fill="url(#title-bottom-fill)">LATERNE</text>
    </g>

    <line class="rule rule-upper" x1="320" y1="698" x2="720" y2="698" stroke="var(--rule-gold)" stroke-width="2"/>
    <line class="rule rule-lower" x1="335" y1="773" x2="728" y2="773" stroke="var(--rule-gold)" stroke-width="2"/>
  </svg>

  <div class="subtitle-block">
    <p class="subtitle-main">Der bemerkenswertesten Gründer und<br>Lenker der Nordregion 2019</p>
    <p class="subtitle-region">Küste und Hinterland</p>
  </div>
</div>
</body>
</html>
```